Brightway Haul & Upkeep Services, are a company that offers a 'one stop shop' pre-move clean up a

I have already selected a logo which I would like on the front of the business cards along with phone numbers, web address and email which are:
0487650392
www.brightwayhaul.com.au
brightwayhaulandupkeep@mailbox.example

On the back of the card I would like to list some of the types of service we offer (clean - move - repairs/maintenance) which are:
CLEAN - windows, gutters, solar panels, driveways/paths, carpets.
MOVE - Small/medium size house/office moves, large item pick-up & delivery, yard clean-up and removal.
General maintenance and repairs.

I would like the blue logo on a gray background.

Thanks

```html
<!DOCTYPE html>
<html lang="en">
<head>
<meta charset="utf-8">
<title>Brightway Haul &amp; Upkeep Services – Business Card</title>
<link rel="stylesheet" href="https://fonts.googleapis.com/css2?family=Open+Sans:wght@400;600;700&display=swap">
<style>
  :root {
    --backdrop: #e4e4e4;
    --card: #ffffff;
    --brand-blue: #2f74b5;
    --band-blue: #7ab8e6;
    --ink: #1c1c1c;
    --rule: #2a2a2a;
  }
  * { box-sizing: border-box; margin: 0; padding: 0; }
  html, body {
    width: 1200px; height: 382px; overflow: hidden;
    background: var(--backdrop);
    font-family: "Open Sans", Arial, sans-serif;
    color: var(--ink);
  }
  .canvas { position: relative; width: 1200px; height: 382px; }
  .card {
    position: absolute; top: 37px;
    width: 539px; height: 307px;
    background: var(--card);
    box-shadow: 0 2px 6px rgba(0,0,0,0.18);
  }
  .card--front { left: 44px; }
  .card--back { left: 629px; }

  .brand-name {
    position: absolute; left: 0; right: 0;
    display: flex; align-items: center; justify-content: center; gap: 14px;
  }
  .brand-name__mark {
    width: 22px; height: 22px; background: var(--brand-blue); flex: none;
  }
  .brand-name__text {
    font-weight: 700; color: var(--brand-blue);
    font-size: 32px; line-height: 1.12; text-align: center;
  }
  .card--front .brand-name { top: 78px; }
  .card--back .brand-name { top: 60px; }
  .card--back .brand-name__text { font-size: 29px; }

  .phone-band {
    position: absolute; left: 0; right: 0; top: 180px; height: 45px;
    border-top: 2px solid var(--rule); border-bottom: 2px solid var(--rule);
  }
  .phone-band__fill {
    position: absolute; left: 0; right: 0; top: 6px; height: 29px;
    background: var(--band-blue);
    display: flex; align-items: center; justify-content: center; gap: 6px;
    font-size: 19px;
  }
  .contact-list {
    position: absolute; left: 0; right: 0; top: 245px;
    list-style: none; text-align: center; font-size: 14.5px; line-height: 24px;
  }
  .contact-list li { display: flex; align-items: center; justify-content: center; gap: 7px; }
  .contact-list svg { flex: none; }

  .services-title {
    position: absolute; left: 0; right: 0; top: 156px;
    text-align: center; color: var(--brand-blue);
    font-size: 21px; font-weight: 600; letter-spacing: 1.6px;
  }
  .service-row {
    position: absolute; left: 30px; right: 20px;
    display: flex; font-size: 13.5px; line-height: 21px;
  }
  .service-row__label {
    color: var(--brand-blue); font-weight: 700; font-size: 15px;
    flex: none; margin-right: 6px;
  }
  .service-row--clean { top: 196px; }
  .service-row--move { top: 223px; }
  .service-row--move .service-row__text { text-align: center; }
  .services-footer {
    position: absolute; left: 0; right: 0; top: 274px;
    text-align: center; color: var(--brand-blue);
    font-size: 16px; font-weight: 600; letter-spacing: 1.2px;
  }
</style>
</head>
<body>
<main class="canvas">
  <section class="card card--front" aria-label="Card front">
    <div class="brand-name">
      <span class="brand-name__mark"></span>
      <span class="brand-name__text">Brightway Haul &amp;<br>Upkeep Services</span>
    </div>
    <div class="phone-band">
      <div class="phone-band__fill">
        <svg width="14" height="14" viewBox="0 0 24 24" aria-hidden="true"><path d="M6.6 10.8a15 15 0 0 0 6.6 6.6l2.2-2.2a1 1 0 0 1 1-.25 11.4 11.4 0 0 0 3.6.6 1 1 0 0 1 1 1V20a1 1 0 0 1-1 1A17 17 0 0 1 3 4a1 1 0 0 1 1-1h3.5a1 1 0 0 1 1 1 11.4 11.4 0 0 0 .6 3.6 1 1 0 0 1-.25 1z" fill="none" stroke="#1c1c1c" stroke-width="2"/></svg>
        <span>0487650392</span>
      </div>
    </div>
    <ul class="contact-list">
      <li><svg width="12" height="12" viewBox="0 0 24 24" aria-hidden="true"><circle cx="12" cy="12" r="10" fill="#2f74b5"/><path d="M2 12h20M12 2c3 3 3 17 0 20M12 2c-3 3-3 17 0 20" stroke="#fff" stroke-width="1.5" fill="none"/></svg>www.brightwayhaul.com.au</li>
      <li><svg width="13" height="11" viewBox="0 0 24 20" aria-hidden="true"><rect x="1" y="3" width="22" height="16" rx="1" fill="#2f74b5"/><path d="M1 4l11 8 11-8" stroke="#fff" stroke-width="1.8" fill="none"/></svg>brightwayhaulandupkeep@mailbox.example</li>
    </ul>
  </section>

  <section class="card card--back" aria-label="Card back">
    <div class="brand-name">
      <span class="brand-name__mark"></span>
      <span class="brand-name__text">Brightway Haul &amp;<br>Upkeep Services</span>
    </div>
    <h2 class="services-title">Services we offer</h2>
    <div class="service-row service-row--clean">
      <span class="service-row__label">CLEAN:</span>
      <span class="service-row__text">Windows, Gutters, Solar Panels, Driveways/paths, Carpets.</span>
    </div>
    <div class="service-row service-row--move">
      <span class="service-row__label">MOVE:</span>
      <span class="service-row__text">Small/medium Size House/office Moves, Large Item Pick-up<br>&amp; Delivery, Yard Clean-up And Removal.</span>
    </div>
    <p class="services-footer">General maintenance and repairs.</p>
  </section>
</main>
</body>
</html>
```